K7 Services business card design contest. Use logo and create a professional layout.

See attached sample. Please sharpen all text and images, don't want any pix-elated content. We are looking for a clean look that quickly provides the information need. Please include our information provided on the sample card. Please feel free to offer any design changes. Please only user the colors provided: #2D3539 & #FFA500. Do not prefer any images other than the K7 Logo

Target Market(s)

Construction, Architects, General Contractors, residential

Industry/Entity Type

Business

Contact Information for Business Card

Company logo, Name, email, fax & phone

Font styles to use
Other font styles liked:
• Josefin Slab

Requirements
Must have
• Name
• Phone & Fax #'s
• address
• Logo
• Website url: www.kq7services.example
Nice to have
• Font Colors #2D3539 & #FFA400
• We prefer a white background.

```html
<!DOCTYPE html>
<html lang="en">
<head>
<meta charset="utf-8">
<title>K7 Services – Business Card</title>
<link href="https://fonts.googleapis.com/css2?family=Montserrat:wght@400;500&display=swap" rel="stylesheet">
<style>
  :root {
    --ink: #2D3539;
    --accent: #FFA500;
    --paper: #FFFFFF;
    --backdrop: #D9D9D9;
  }
  * { margin: 0; padding: 0; box-sizing: border-box; }
  html, body {
    width: 1200px; height: 852px; overflow: hidden;
    background: var(--backdrop);
    font-family: "Montserrat", sans-serif;
    color: var(--ink);
  }
  .sheet {
    position: relative; width: 1200px; height: 852px;
    display: flex; align-items: center; justify-content: center; gap: 40px;
  }
  .card {
    position: relative; width: 540px; height: 309px;
    background: var(--paper); border-radius: 14px; overflow: hidden;
    box-shadow: 0 6px 18px rgba(0,0,0,.18);
  }
  .brand { display: flex; align-items: center; gap: 12px; }
  .brand-mark { width: 26px; height: 26px; background: var(--ink); border-radius: 50%; }
  .brand-name { font-weight: 400; font-size: 38px; color: var(--ink); letter-spacing: 2px; }
  .card-front { display: flex; align-items: center; justify-content: center; }
  .card-back .wave { position: absolute; inset: 0; }
  .card-back .brand { position: absolute; top: 22px; right: 44px; gap: 9px; }
  .card-back .brand-mark { width: 18px; height: 18px; }
  .card-back .brand-name { font-size: 26px; letter-spacing: 1.5px; }
  .person { position: absolute; left: 34px; top: 112px; }
  .person-name { color: var(--accent); font-size: 17px; font-weight: 400; }
  .person-title { font-size: 12px; margin-top: 4px; }
  .contact { position: absolute; left: 34px; top: 182px; font-size: 11.5px; line-height: 1.5; }
  .contact-line { display: flex; align-items: center; gap: 8px; }
  .contact-line svg { width: 12px; height: 12px; fill: var(--accent); flex: none; }
  .address { margin-bottom: 4px; }
  .services {
    position: absolute; right: 22px; top: 160px; text-align: right;
    color: var(--accent); font-size: 13px; line-height: 1.5; letter-spacing: 1px;
  }
  .services li { list-style: none; }
  .services li::after { content: " «"; color: var(--paper); }
</style>
</head>
<body>
<main class="sheet">
  <section class="card card-front">
    <div class="brand">
      <span class="brand-mark"></span>
      <span class="brand-name">K7 Services</span>
    </div>
  </section>

  <section class="card card-back">
    <svg class="wave" viewBox="0 0 540 309" preserveAspectRatio="none" aria-hidden="true">
      <path d="M0 292 C140 292 280 276 360 240 C300 282 150 300 0 304 Z" fill="var(--accent)"/>
      <path d="M540 80 C460 95 430 150 410 205 C385 265 330 298 220 309 L540 309 Z" fill="var(--ink)"/>
      <path d="M540 66 C452 82 418 140 396 198 C370 262 310 292 180 304" fill="none" stroke="var(--accent)" stroke-width="5"/>
    </svg>

    <div class="brand">
      <span class="brand-mark"></span>
      <span class="brand-name">K7 Services</span>
    </div>

    <div class="person">
      <p class="person-name">Daniel R. Mercer, MBA</p>
      <p class="person-title">Director of Operations</p>
    </div>

    <div class="contact">
      <p class="address">1720 Larkspur Road, Suite<br>210-418 Maple Falls, Georgia, 30012</p>
      <p class="contact-line">
        <svg viewBox="0 0 24 24"><path d="M6.6 10.8a15 15 0 0 0 6.6 6.6l2.2-2.2a1 1 0 0 1 1-.25 11.4 11.4 0 0 0 3.6.6 1 1 0 0 1 1 1V20a1 1 0 0 1-1 1A17 17 0 0 1 3 4a1 1 0 0 1 1-1h3.5a1 1 0 0 1 1 1 11.4 11.4 0 0 0 .6 3.6 1 1 0 0 1-.25 1z"/></svg>
        (555) 014 - 2290
      </p>
      <p class="contact-line">
        <svg viewBox="0 0 24 24"><path d="M6 2h9l3 3v5H6zM4 11h16a2 2 0 0 1 2 2v7a2 2 0 0 1-2 2H4a2 2 0 0 1-2-2v-7a2 2 0 0 1 2-2zm2 3v2h4v-2z"/></svg>
        (555) 018 - 3367
      </p>
      <p class="contact-line">
        <svg viewBox="0 0 24 24"><path d="M12 2a10 10 0 1 0 0 20 10 10 0 0 0 0-20zm6.9 6h-3a15 15 0 0 0-1.3-3.9A8 8 0 0 1 18.9 8zM12 4c.8 1.2 1.5 2.5 1.9 4h-3.8c.4-1.5 1.1-2.8 1.9-4zM4.3 14a8 8 0 0 1 0-4h3.4a16 16 0 0 0 0 4zm.8 2h3a15 15 0 0 0 1.3 3.9A8 8 0 0 1 5.1 16zm3-8h-3a8 8 0 0 1 4.3-3.9A15 15 0 0 0 8.1 8zM12 20c-.8-1.2-1.5-2.5-1.9-4h3.8c-.4 1.5-1.1 2.8-1.9 4zm2.3-6H9.7a14 14 0 0 1 0-4h4.6a14 14 0 0 1 0 4zm.3 5.9a15 15 0 0 0 1.3-3.9h3a8 8 0 0 1-4.3 3.9zM16.3 14a16 16 0 0 0 0-4h3.4a8 8 0 0 1 0 4z"/></svg>
        www.kq7services.example
      </p>
    </div>

    <ul class="services">
      <li>VIDEO</li>
      <li>DRONE</li>
      <li>WEBCAM</li>
    </ul>
  </section>
</main>
</body>
</html>
```